Client Meeting and installation Email Follow up

I would like a follow-up email template created.
Currently, we do a lot of new construction builds and meet with clients about 6-3 months before they take possession of their new house. I want a follow-up email template to be sent after the homeowner takes possession of their house that enquires if the clients are happy about their new lighting, the service they received, and their customer service representative with Brightwell Lamps and Breezes. I have attached a few files of what our current marketing looks like.
Target Market(s)
Home Owners We have already met with
Industry/Entity Type
Residential lighting
Font styles to use
Other font styles liked:
- Alta Light, Playfair Display, Montserrat
Colors
Designer to choose colors to be used in the design.
Look and feel
Each slider illustrates characteristics of the customer's brand and the style your logo design should communicate.

```html
<!DOCTYPE html>
<html lang="en">
<head>
<meta charset="utf-8">
<title>Brightwell Lamps and Breezes – Follow-up</title>
<link href="https://fonts.googleapis.com/css2?family=Oswald:wght@300;400;500&family=Jost:wght@300;400;600&display=swap" rel="stylesheet">
<style>
  :root {
    --ink: #1f1f1f;
    --text: #3a3a3a;
    --white: #ffffff;
    --band: #efeeee;
    --accent: #d7bba6;
    --footer: #262626;
    --line: #2a2a2a;
  }
  * { margin: 0; padding: 0; box-sizing: border-box; }
  html, body { width: 1200px; height: 3771px; overflow: hidden; background: var(--white); }
  .email { position: relative; width: 1200px; height: 3771px; font-family: "Jost", sans-serif; color: var(--text); }
  .abs { position: absolute; }

  .brand { top: 44px; left: 0; width: 1200px; text-align: center; display: flex; justify-content: center; align-items: center; gap: 16px; }
  .brand-mark { width: 30px; height: 30px; background: var(--ink); }
  .brand-name { font-family: "Oswald", sans-serif; font-weight: 400; font-size: 48px; letter-spacing: 1px; color: var(--ink); text-transform: uppercase; line-height: 1; }

  .photo { background: linear-gradient(135deg, #e9e4dd, #c9bcab); }
  .hero-kitchen { left: 0; top: 188px; width: 390px; height: 660px; background: linear-gradient(160deg, #f2f1ee 0%, #e1dbd2 55%, #b49a7c 100%); }
  .frame { background: #f7f7f7; border: 3px solid #e3e3e3; box-shadow: 0 0 4px rgba(0,0,0,.15); }
  .frame-inner { position: absolute; }
  .hero-leaves { left: 870px; top: 180px; width: 330px; height: 520px; background: radial-gradient(ellipse at 70% 30%, rgba(120,180,60,.55), rgba(120,180,60,.15) 55%, rgba(255,255,255,0) 75%); }

  .hero-kicker { left: 740px; top: 322px; font-family: "Oswald", sans-serif; font-weight: 300; font-size: 48px; color: var(--ink); line-height: 1; }
  .hero-title { left: 737px; top: 392px; font-family: "Oswald", sans-serif; font-weight: 400; font-size: 90px; line-height: 100px; color: var(--ink); text-transform: uppercase; }
  .hero-text { left: 740px; top: 615px; width: 420px; font-size: 24px; line-height: 41px; color: var(--ink); }

  .section-title { left: 0; width: 1200px; text-align: center; font-family: "Oswald", sans-serif; font-weight: 400; font-size: 47px; color: var(--ink); line-height: 1; }
  .intro-text { left: 120px; top: 1096px; width: 960px; text-align: center; font-weight: 300; font-size: 24px; line-height: 41px; letter-spacing: .6px; }

  .services { left: 0; top: 1405px; width: 1200px; height: 853px; background: linear-gradient(180deg, #f1f1f1, #ebe9e8 60%, #e6e4e2); }
  .step-num { width: 133px; height: 133px; border-radius: 50%; background: var(--accent); display: flex; align-items: center; justify-content: center; font-family: "Jost", sans-serif; font-weight: 600; font-size: 48px; color: var(--ink); }
  .step-title { font-family: "Oswald", sans-serif; font-weight: 400; font-size: 28px; color: var(--ink); line-height: 1; }
  .step-text { font-weight: 300; font-size: 26px; line-height: 41px; color: var(--text); }

  .feedback-title { left: 88px; top: 2380px; font-family: "Oswald", sans-serif; font-weight: 500; font-size: 49px; color: var(--ink); line-height: 1; }
  .feedback-text { left: 88px; top: 2464px; width: 520px; font-weight: 300; font-size: 26px; line-height: 41px; }
  .feedback-photo { left: 643px; top: 2377px; width: 484px; height: 506px; background: linear-gradient(180deg, #e8e3dc 0%, #c8b7a3 45%, #8c5a3a 100%); }

  .offer-brand { left: 0; top: 2972px; width: 1200px; text-align: center; font-weight: 300; font-size: 62px; color: var(--ink); line-height: 1; }
  .offer-rule { left: 255px; top: 3078px; width: 691px; height: 3px; background: var(--line); }
  .offer-amount { left: 0; top: 3112px; width: 1200px; text-align: center; font-weight: 300; font-size: 150px; color: var(--ink); line-height: 1; }
  .field { top: 3292px; width: 317px; height: 74px; background: var(--white); box-shadow: 0 2px 8px rgba(0,0,0,.12); font-size: 22px; color: var(--text); padding-left: 28px; display: flex; align-items: center; }
  .submit { left: 520px; top: 3405px; width: 161px; height: 72px; background: var(--ink); color: var(--white); font-weight: 600; font-size: 25px; display: flex; align-items: center; justify-content: center; }

  .footer { left: 0; top: 3565px; width: 1200px; height: 206px; background: var(--footer); color: var(--white); }
  .footer-note { position: absolute; top: 64px; width: 1200px; text-align: center; font-size: 24px; }
  .social { position: absolute; top: 136px; left: 500px; width: 200px; display: flex; justify-content: space-between; }
  .social span { width: 34px; height: 34px; border-radius: 50%; border: 3px solid var(--white); }
</style>
</head>
<body>
<div class="email">

  <header class="abs brand">
    <span class="brand-mark"></span>
    <span class="brand-name">Brightwell Lamps &amp; Breezes</span>
  </header>

  <div class="abs hero-kitchen" role="img" aria-label="Bright white kitchen with pendant light and island"></div>
  <div class="abs frame" style="left:387px;top:185px;width:206px;height:255px;">
    <div class="frame-inner photo" style="left:32px;top:31px;width:135px;height:189px;background:linear-gradient(180deg,#8c8f92,#c49a5a);" role="img" aria-label="Geometric pendant bulbs glowing"></div>
  </div>
  <div class="abs frame" style="left:405px;top:444px;width:263px;height:201px;">
    <div class="frame-inner photo" style="left:27px;top:32px;width:195px;height:132px;" role="img" aria-label="Open dining room with lighting"></div>
  </div>
  <div class="abs frame" style="left:300px;top:648px;width:267px;height:201px;">
    <div class="frame-inner photo" style="left:32px;top:32px;width:193px;height:129px;background:linear-gradient(135deg,#f1f1f1,#d6d2cb);" role="img" aria-label="Bright bedroom with ceiling fan"></div>
  </div>
  <div class="abs hero-leaves" role="img" aria-label="Green leaves decoration"></div>

  <div class="abs hero-kicker">WELCOME TO</div>
  <h1 class="abs hero-title">Brightwell<br>Lamps</h1>
  <p class="abs hero-text">Lorem ipsum dolor sit amet, consectetur adipiscing elit, sed do eiusmod tempor incididunt ut</p>

  <h2 class="abs section-title" style="top:1000px;">Happy About Their New Lighting</h2>
  <p class="abs intro-text">Congratulations on the recent move into your new home! We hope you’re settling in well and enjoying your new space.<br>At Brightwell Lamps and Breezes, we’re dedicated to ensuring that every detail of your lighting installation meets your expectations. We’d love to hear about your experience with our services and the installation process.</p>

  <section class="abs services" role="img" aria-label="Faded living room with ceiling fan in background"></section>
  <h2 class="abs section-title" style="top:1516px;">Our Services</h2>

  <div class="abs step-num" style="left:105px;top:1632px;">1</div>
  <h3 class="abs step-title" style="left:297px;top:1620px;">Your Satisfaction with the Lighting</h3>
  <p class="abs step-text" style="left:301px;top:1666px;width:790px;">Are you pleased with how the lighting enhances your new home? Are there any adjustments or additional features you would like to discuss?</p>

  <h3 class="abs step-title" style="left:108px;top:1821px;">The Installation Process</h3>
  <p class="abs step-text" style="left:108px;top:1867px;width:780px;">Did our team meet your expectations during the installation? Was the process smooth and professional?</p>
  <div class="abs step-num" style="left:914px;top:1823px;">2</div>

  <div class="abs step-num" style="left:105px;top:2011px;">3</div>
  <h3 class="abs step-title" style="left:299px;top:2011px;">Customer Service Experience</h3>
  <p class="abs step-text" style="left:301px;top:2059px;width:790px;">How did you find working with your Brightwell Lamps and Breezes representative? Were they helpful and responsive to your needs?</p>

  <h2 class="abs feedback-title">Your feedback</h2>
  <p class="abs feedback-text">Your feedback is invaluable to us as it helps us continually improve our services. If there’s anything you’d like to discuss or if you need further assistance, please don’t hesitate to reach out. Thank you for choosing Brightwell Lamps and Breezes for your new home. We look forward to hearing from you and hope you continue to enjoy your beautifully lit space!</p>
  <div class="abs feedback-photo" role="img" aria-label="Living room with ceiling fan, stone fireplace and leather sofas"></div>

  <div class="abs offer-brand">Brightwell Lamps and Breezes</div>
  <div class="abs offer-rule"></div>
  <div class="abs offer-amount">10% OFF</div>
  <div class="abs field" style="left:266px;">Name</div>
  <div class="abs field" style="left:618px;">Your Position</div>
  <div class="abs submit">Submit</div>

  <footer class="abs footer">
    <p class="footer-note">©Copyrights 2024 Company Name &nbsp;&nbsp;|&nbsp;&nbsp;&nbsp; All Rights Reserved</p>
    <div class="social"><span></span><span></span><span></span><span></span></div>
  </footer>

</div>
</body>
</html>
```